home accents e-commerce website

I'd like a professional simple website designed where I can sell my home goods. I already have my domain name registered. I need the website to accept credit card payments and Monvex. It should have a shopping cart option and calculate sales tax and shipping costs on merchandise automatically.

I'll be taking photographs of the merchandise and writing product descriptions myself. (I'm not a professional photographer, so these photos probably won't look too polished. If you can help me make them look better, that'd be great). As I add new merchandise in the future, I'd like an option where I can log in to the back end myself and add pictures/product descriptions. And take old products down as they sell out. So the website needs to be user-friendly for me, even though I'm completely web design illiterate!

I'd like a creative, talented person who can create a whimsical, cute website. Nothing too corporate-looking.

Thank you!

Target Market(s)

women, online shoppers, New York City-area, (ship products to the United States only)

Industry/Entity Type

Home And Garden

Coding

Coded - Design and coding required

Number of Pages Required

1 page

Font styles to use
Sans Serif

Colors
0355a3
ffffff

Requirements
Must have
• shopping cart feature
• safe, secure credit card and Monvex payments
• ability for me to go in and add new products and take down old/sold products
Nice to have
• whimsical, cute design
Should not have
• too corporate-looking

```html
<!DOCTYPE html>
<html lang="en">
<head>
<meta charset="utf-8">
<title>nestly home goods</title>
<link rel="stylesheet" href="https://fonts.googleapis.com/css2?family=Mulish:wght@400;600;700&family=Open+Sans:wght@400;600;700&display=swap">
<style>
:root{
  --blue:#0355a3;
  --blue-dark:#02468a;
  --blue-soft:#dbe6f3;
  --white:#ffffff;
  --ink:#333a44;
  --muted:#8a8f96;
  --line:#d9dde2;
  --grey-band:#ececec;
}
*{box-sizing:border-box;margin:0;padding:0}
html,body{width:1200px;height:2507px;overflow:hidden;background:var(--white)}
body{position:relative;font-family:"Open Sans",Arial,sans-serif;color:var(--ink)}
a{color:inherit;text-decoration:none}
ul{list-style:none}
.abs{position:absolute}

/* top bar */
.topbar{position:absolute;left:0;top:0;width:1200px;height:43px;background:var(--blue)}
.social-mini{position:absolute;left:793px;top:9px;display:flex;gap:6px}
.social-mini span{width:24px;height:24px;border:1.5px solid var(--white);border-radius:50%}
.cart{position:absolute;left:960px;top:0;width:112px;height:43px;background:var(--blue-dark);color:var(--white);font-size:13px;display:flex;align-items:center;justify-content:center;gap:8px}

/* header */
.header{position:absolute;top:43px;left:0;width:1200px;height:105px}
.brand{position:absolute;left:125px;top:18px;color:var(--blue);font-family:"Mulish",sans-serif;font-weight:700;text-align:center;line-height:1}
.brand .name{font-size:52px;letter-spacing:1px}
.brand .sub{font-size:16px;letter-spacing:6px;margin-top:4px;font-weight:400}
.nav{position:absolute;right:150px;top:40px;display:flex;gap:50px;font-family:"Mulish",sans-serif;font-size:20px;color:#555}

/* hero */
.hero{position:absolute;top:148px;left:0;width:1200px;height:587px;background:linear-gradient(100deg,#e3e7ea 0%,#cfd8dd 30%,#b9cdd6 55%,#d8c3ad 100%)}
.hero-photo{position:absolute;left:575px;top:60px;width:540px;height:360px;border-radius:20px;background:radial-gradient(ellipse at 40% 50%,#d9cdb2 0%,#5ea6c9 55%,rgba(180,170,160,0) 75%)}
.hero-text{position:absolute;left:128px;top:148px}
.hero-text h1{font-family:"Mulish",sans-serif;font-weight:400;font-size:41px;color:var(--blue)}
.hero-text h2{font-family:"Mulish",sans-serif;font-weight:400;font-size:28px;color:#2b2f36;margin-top:2px}
.hero-text p{font-size:16px;color:#555;line-height:1.6;width:420px;margin-top:14px}
.btn{display:inline-block;background:var(--blue);color:var(--white);font-weight:700;font-size:13px;text-transform:uppercase}
.hero-text .btn{margin-top:22px;padding:11px 26px;border-radius:2px}
.dots{position:absolute;left:558px;top:477px;display:flex;gap:10px}
.dots span{width:14px;height:14px;border-radius:50%;background:var(--white)}
.dots span:first-child{background:none;border:2px solid var(--white)}
.wave{position:absolute;left:0;top:640px}

/* sidebar */
.categories{position:absolute;left:117px;top:760px;width:249px;height:415px;background:var(--blue);color:var(--white)}
.categories h3{height:50px;background:#0d62b5;font-family:"Mulish",sans-serif;font-weight:400;font-size:24px;padding:10px 0 0 34px}
.categories ul{padding:22px 0 0 36px}
.categories li{font-size:16px;height:34.6px;display:flex;align-items:center;gap:12px}
.categories li::before{content:"";border-left:5px solid var(--white);border-top:4px solid transparent;border-bottom:4px solid transparent}
.offer{position:absolute;left:115px;top:1190px;width:251px;height:276px;border:2px solid var(--line);background:var(--white)}
.offer-photo{height:150px;background:linear-gradient(135deg,#2d4a7a 0%,#4c6f9f 40%,#e9e4dc 70%,#c8a58a 100%)}
.offer-body{padding:8px 20px}
.offer small{display:block;color:var(--blue);font-family:"Mulish",sans-serif;font-size:17px}
.offer strong{display:block;color:var(--blue);font-family:"Mulish",sans-serif;font-weight:600;font-size:25px;line-height:1.1}
.offer .outline{display:inline-block;margin-top:10px;border:2px solid var(--blue);color:var(--blue);font-size:12px;font-weight:600;padding:4px 16px}

/* products */
.section-title{font-family:"Mulish",sans-serif;font-weight:400;font-size:28px;color:#2b2f36}
.latest-title{position:absolute;left:398px;top:766px}
.card{position:absolute;border:1.5px solid var(--line);background:var(--white);text-align:center}
.card .photo{margin:10px auto 0;border-radius:4px}
.card .name{font-family:"Mulish",sans-serif;font-size:19px;color:#3a3f46}
.card .desc{font-size:12px;color:var(--muted);margin-top:2px}
.card .buy{position:absolute;left:0;bottom:0;width:100%;height:38px;display:flex}
.card .price{flex:0 0 42%;background:var(--blue-soft);color:var(--blue);font-size:16px;display:flex;align-items:center;justify-content:center}
.card .btn{flex:1;display:flex;align-items:center;justify-content:center;text-transform:none;font-size:15px;font-weight:600}
.latest .card{width:216px;height:307px}
.latest .photo{width:180px;height:160px}
.latest .name{margin-top:24px}

/* top sellings */
.top-band{position:absolute;left:0;top:1532px;width:1200px;height:485px;background:linear-gradient(90deg,#b7c4d4 0%,#d8dee6 35%,#e4dcd5 65%,#c3ccd8 100%);border-top:1.5px dashed #a9b3bf;border-bottom:1.5px dashed #a9b3bf}
.top-title{position:absolute;left:0;width:1200px;top:1572px;text-align:center}
.top .card{width:221px;height:314px;top:1633px}
.top .photo{width:190px;height:170px}
.top .name{margin-top:20px}

/* newsletter */
.newsletter{position:absolute;left:0;top:2017px;width:1200px;height:102px;background:var(--grey-band)}
.newsletter h3{position:absolute;left:218px;top:32px;font-family:"Mulish",sans-serif;font-weight:400;font-size:28px;color:#2b2f36}
.newsletter .field{position:absolute;left:486px;top:33px;width:398px;height:38px;background:var(--white);border:1px solid #cfd3d8;font-size:13px;color:#999;padding:10px 16px}
.newsletter .btn{position:absolute;left:883px;top:33px;width:113px;height:38px;text-transform:none;font-size:16px;font-weight:600;display:flex;align-items:center;justify-content:center}

/* footer */
.footer-brand{position:absolute;left:135px;top:2168px}
.fcol{position:absolute;top:2172px}
.fcol h4{font-family:"Mulish",sans-serif;font-weight:600;font-size:20px;color:var(--blue);text-transform:uppercase}
.fcol li{font-size:16px;color:#666;margin-top:12px;line-height:18px}
.fcol li:first-child{margin-top:16px}
.social{display:flex;gap:10px;margin-top:16px}
.social span{width:38px;height:38px;border:2px solid var(--blue);border-radius:50%}
.cards{display:flex;gap:10px;margin-top:16px}
.cards span{width:44px;height:22px;border:1px solid var(--line);font-size:9px;font-weight:700;color:var(--blue);display:flex;align-items:center;justify-content:center}
.rule{position:absolute;left:117px;top:2433px;width:966px;border-top:1px solid var(--line)}
.copy{position:absolute;left:0;width:1200px;top:2456px;text-align:center;font-size:14px;color:#666}
</style>
</head>
<body>

<div class="topbar">
  <div class="social-mini" aria-label="Social links"><span></span><span></span><span></span><span></span></div>
  <a class="cart" href="#">
    <svg width="22" height="18" viewBox="0 0 22 18" fill="none" stroke="#fff" stroke-width="1.6"><path d="M1 1h3l3 11h11l3-8H6"/><circle cx="8" cy="15.5" r="1.5"/><circle cx="17" cy="15.5" r="1.5"/></svg>
    0 ITEMS
  </a>
</div>

<header class="header">
  <div class="brand"><div class="name">nestly</div><div class="sub">HOME GOODS</div></div>
  <nav class="nav"><a href="#">About nestly</a><a href="#">How does this craziness work?</a><a href="#">Contact</a></nav>
</header>

<section class="hero">
  <div class="hero-photo" role="img" aria-label="Decorative jewellery boxes in a softly blurred living room"></div>
  <div class="hero-text">
    <h1>Special Home Goods</h1>
    <h2>for your Dream Home</h2>
    <p>Class aptent taciti sociosqu ad litora torquent per conubia nostra per inceptos hymenaeos</p>
    <a class="btn" href="#">Read more</a>
  </div>
  <div class="dots"><span></span><span></span><span></span><span></span></div>
</section>
<svg class="wave" width="1200" height="100" viewBox="0 0 1200 100" aria-hidden="true">
  <path d="M0 60 Q600 -20 1200 60 L1200 100 L0 100Z" fill="#fff"/>
  <path d="M0 40 Q600 -30 1200 50" fill="none" stroke="#fff" stroke-width="2" opacity=".8"/>
</svg>

<aside class="categories">
  <h3>Categories</h3>
  <ul>
    <li>Vases</li><li>Throw Pillows</li><li>Blankets and Throws</li><li>For Your Floors</li><li>For Your Walls</li><li>For Your Table</li><li>For Your Bedside</li><li>Let THere Be Light</li><li>Put Your Feet Up</li>
  </ul>
</aside>
<div class="offer">
  <div class="offer-photo" role="img" aria-label="Colourful children's bedroom with wardrobe and wall shelves"></div>
  <div class="offer-body">
    <small>Special Offer</small>
    <strong>Get 20% off Now</strong>
    <a class="outline" href="#">Click here</a>
  </div>
</div>

<h2 class="section-title latest-title">Latest Products</h2>
<div class="latest">
  <div class="card" style="left:401px;top:824px"><div class="photo" role="img" aria-label="Blue patterned throw pillow" style="background:radial-gradient(#7fb9c4,#e9f1f2 70%)"></div><div class="name">Product Name</div><div class="desc">Eget fermentum et lorem</div><div class="buy"><span class="price">$15.99</span><a class="btn" href="#">Buy Now</a></div></div>
  <div class="card" style="left:633px;top:824px"><div class="photo" role="img" aria-label="Wall planter with red flowers" style="background:radial-gradient(#b5302b,#5d6b3a 45%,#f4f1ec 72%)"></div><div class="name">Product Name</div><div class="desc">Eget fermentum et lorem</div><div class="buy"><span class="price">$15.99</span><a class="btn" href="#">Buy Now</a></div></div>
  <div class="card" style="left:866px;top:824px"><div class="photo" role="img" aria-label="Succulent in a concrete pot" style="background:radial-gradient(#7fa65a,#c9cbc8 45%,#f6f6f5 72%)"></div><div class="name">Product Name</div><div class="desc">Eget fermentum et lorem</div><div class="buy"><span class="price">$15.99</span><a class="btn" href="#">Buy Now</a></div></div>
  <div class="card" style="left:401px;top:1156px"><div class="photo" role="img" aria-label="White daisies in a brown vase" style="background:radial-gradient(#f3e9c9,#6e5a4c 50%,#f7f6f4 74%)"></div><div class="name">Product Name</div><div class="desc">Eget fermentum et lorem</div><div class="buy"><span class="price">$15.99</span><a class="btn" href="#">Buy Now</a></div></div>
  <div class="card" style="left:633px;top:1156px"><div class="photo" role="img" aria-label="Orange lilies in a dark blue vase" style="background:radial-gradient(#f08a28,#1e2a55 50%,#f7f6f4 74%)"></div><div class="name">Product Name</div><div class="desc">Eget fermentum et lorem</div><div class="buy"><span class="price">$15.99</span><a class="btn" href="#">Buy Now</a></div></div>
  <div class="card" style="left:866px;top:1156px"><div class="photo" role="img" aria-label="Red rug" style="background:radial-gradient(ellipse 60% 20%,#9c1d1a 60%,#faf9f8 100%)"></div><div class="name">Product Name</div><div class="desc">Eget fermentum et lorem</div><div class="buy"><span class="price">$15.99</span><a class="btn" href="#">Buy Now</a></div></div>
</div>

<div class="top-band" role="img" aria-label="Softly blurred interior photo background"></div>
<h2 class="section-title top-title">Top Sellings</h2>
<div class="top">
  <div class="card" style="left:130px"><div class="photo" role="img" aria-label="Pink checked pillow" style="background:radial-gradient(#c0245d,#e9b8c9 45%,#fff 72%)"></div><div class="name">Product Name</div><div class="desc">Eget fermentum et lorem</div><div class="buy"><span class="price">$15.99</span><a class="btn" href="#">Buy Now</a></div></div>
  <div class="card" style="left:374px"><div class="photo" role="img" aria-label="Plaid throw blanket" style="background:radial-gradient(#5a4a40,#c9bfb4 45%,#fff 72%)"></div><div class="name">Product Name</div><div class="desc">Eget fermentum et lorem</div><div class="buy"><span class="price">$15.99</span><a class="btn" href="#">Buy Now</a></div></div>
  <div class="card" style="left:618px"><div class="photo" role="img" aria-label="Round jute rug" style="background:radial-gradient(ellipse 55% 18%,#c8ad86 70%,#fff 100%)"></div><div class="name">Product Name</div><div class="desc">Eget fermentum et lorem</div><div class="buy"><span class="price">$15.99</span><a class="btn" href="#">Buy Now</a></div></div>
  <div class="card" style="left:861px"><div class="photo" role="img" aria-label="Children's table and chairs" style="background:radial-gradient(#f2a8c4,#b6d98a 45%,#fff 72%)"></div><div class="name">Product Name</div><div class="desc">Eget fermentum et lorem</div><div class="buy"><span class="price">$15.99</span><a class="btn" href="#">Buy Now</a></div></div>
</div>

<section class="newsletter">
  <h3>Join Our Newsletter</h3>
  <div class="field">Email address</div>
  <a class="btn" href="#">Subscribe</a>
</section>

<footer>
  <div class="brand footer-brand" style="left:135px;top:2168px"><div class="name">nestly</div><div class="sub">HOME GOODS</div></div>
  <div class="fcol" style="left:401px"><h4>Quick Links</h4><ul><li>Home</li><li>About nestly</li><li>How does this craziness work?</li><li>Contact</li></ul></div>
  <div class="fcol" style="left:687px"><h4>Resources</h4><ul><li>My Account</li><li>My Cart</li><li>Register</li><li>Sign In</li></ul></div>
  <div class="fcol" style="left:886px"><h4>Stay in Touch</h4>
    <div class="social" aria-label="Social links"><span></span><span></span><span></span><span></span></div>
    <div class="cards" aria-label="Accepted payments"><span>Veltra</span><span>Amberline</span><span>Corvane</span><span>Monvex</span></div>
  </div>
  <div class="rule"></div>
  <div class="copy">© 2017 Company Name&nbsp; All right reserved</div>
</footer>

</body>
</html>
```